Refresh of far from plain IT company website

Our web site is starting to show it's age. You can see the existing site here: www.plumbwick.net. As a growing company we want to come across as a dynamic collection of IT experts.

We want to update the design so are open to any colour palette and look, but want to retain our current table logo. We use the logo on our business cards but with a white background - see the attached file, so you don't need to keep the brown or the green.

The design should consider the range of browsers that will be looking at the site - so please show how it will look on a wide screen laptop and a 768x1024 tablet.

We want to add some pages about our team and their skills, probably with photos of each person on the team.

This is an uncoded project - the PSD files of the design is required, not coding.
Updates

Thanks everyone for the submissions so far.  It's a holiday day in the UK today but we will get some feedback on the designs so far out to you.

Target Market(s)

Architects and other creative types looking for IT support

Industry/Entity Type

Business

Font styles to use
Serif
Sans Serif

Requirements
Must have
• Must look good on a laptop and an iPad.

```html
<!DOCTYPE html>
<html lang="en">
<head>
<meta charset="utf-8">
<title>plumbwick – far from plain IT company</title>
<link href="https://fonts.googleapis.com/css2?family=Source+Sans+3:wght@400;600&display=swap" rel="stylesheet">
<style>
:root{
  --brand:#9c0c5b;
  --brand-dark:#86094d;
  --accent:#f0b400;
  --ink:#4a4a4a;
  --muted:#777;
  --line:#e3e3e3;
  --panel:#f4f4f4;
  --footer:#3b3b3b;
  --white:#fff;
}
*{box-sizing:border-box;margin:0;padding:0}
html,body{width:870px;height:1200px;overflow:hidden;background:var(--white)}
body{position:relative;font-family:"Source Sans 3",Arial,sans-serif;color:var(--ink)}
.abs{position:absolute}

.site-header{left:0;top:0;width:870px;height:61px}
.brand{left:94px;top:16px;display:flex;align-items:center;gap:10px}
.brand-mark{width:28px;height:20px;background:var(--accent)}
.brand-name{font-size:26px;font-weight:600;color:var(--brand);letter-spacing:.2px}
.search{left:614px;top:18px;width:161px;height:27px;border:1px solid #d8d8d8;border-radius:2px}
.search svg{position:absolute;right:6px;top:5px}

.main-nav{left:0;top:61px;width:870px;height:35px;background:var(--brand)}
.main-nav ul{list-style:none;position:absolute;left:103px;top:0;display:flex;height:35px;align-items:center;font-size:10px;color:var(--white)}
.main-nav li{margin-right:0}
.main-nav .current{color:var(--accent)}

.hero{left:0;top:96px;width:870px;height:411px;background:linear-gradient(100deg,#dcdcdc 0%,#f2f2f2 35%,#e8e4e0 60%,#c9c9c9 100%)}
.hero-arrow{top:291px;width:37px;height:37px;border-radius:50%;background:rgba(60,60,60,.75)}
.hero-arrow svg{position:absolute;left:12px;top:11px}

.service{top:557px;width:160px;height:153px;background:linear-gradient(#fff,#f6f6f6);border:1px solid #ececec;box-shadow:0 3px 4px rgba(0,0,0,.08);text-align:center}
.service svg{margin-top:14px}
.service h3{font-size:12.5px;font-weight:400;color:var(--brand);margin-top:6px}
.service p{font-size:8.5px;line-height:13px;color:var(--muted);margin:8px 8px 0}

.about{left:95px;top:756px;width:450px}
.section-title{font-size:17px;font-weight:400;color:#444;text-transform:uppercase}
.about p{font-size:9.5px;line-height:16px;color:#666;margin-top:9px}
.about p+p{margin-top:17px}
.btn{display:inline-block;margin-top:17px;background:var(--brand);color:var(--white);font-size:8.5px;padding:7px 13px;text-transform:uppercase}

.news{left:558px;top:748px;width:218px;height:231px;background:var(--panel)}
.news h2{position:absolute;left:12px;top:13px;font-size:15px;font-weight:400;color:var(--brand)}
.news .more{position:absolute;right:16px;top:18px}
.news-item{position:absolute;left:13px;width:200px;display:flex;gap:12px}
.date{width:37px;height:37px;background:#e2e2e2;text-align:center;color:#555;flex:none}
.date b{display:block;font-size:14px;font-weight:400;line-height:20px;margin-top:2px}
.date span{display:block;font-size:8px;color:#888}
.news-item p{font-size:8.5px;line-height:13px;color:#888}

.clients-title{left:95px;top:1003px}
.client{top:1038px;height:57px;border:1px solid #dcdcdc;display:flex;align-items:center;justify-content:center;font-size:15px;font-weight:600;color:#555}
.clients-next{left:756px;top:1056px}

.site-footer{left:0;top:1128px;width:870px;height:72px;background:var(--footer)}
.foot-nav{position:absolute;left:95px;top:20px;font-size:9.5px;color:#ddd;word-spacing:2px}
.foot-nav span{color:#999;margin:0 6px}
.copyright{position:absolute;left:95px;top:43px;font-size:8.5px;color:#ccc}
.social{position:absolute;left:678px;top:25px;display:flex;gap:4px}
.social span{width:20px;height:20px;border-radius:50%;background:#e6e6e6;display:block}
</style>
</head>
<body>

<header class="site-header abs">
  <div class="brand abs"><span class="brand-mark"></span><span class="brand-name">plumbwick</span></div>
  <div class="search abs"><svg width="16" height="16" viewBox="0 0 16 16"><circle cx="6" cy="6" r="4.5" fill="none" stroke="#444" stroke-width="1.8"/><line x1="9.5" y1="9.5" x2="14.5" y2="14.5" stroke="#444" stroke-width="2.6" stroke-linecap="round"/></svg></div>
</header>

<nav class="main-nav abs">
  <ul>
    <li class="current" style="width:63px">Home</li>
    <li style="width:81px">About us</li>
    <li style="width:87px">What we do</li>
    <li style="width:82px">News blog</li>
    <li style="width:70px">Articles</li>
    <li style="width:68px">Clients</li>
    <li style="width:71px">Partners</li>
    <li>Contact Us</li>
  </ul>
</nav>

<section class="hero abs" role="img" aria-label="Photo of four colleagues in white shirts working together at a laptop in a bright office">
  <div class="hero-arrow abs" style="left:74px"><svg width="12" height="14" viewBox="0 0 12 14"><polyline points="9,1 3,7 9,13" fill="none" stroke="#fff" stroke-width="1.5"/></svg></div>
  <div class="hero-arrow abs" style="left:759px"><svg width="12" height="14" viewBox="0 0 12 14"><polyline points="3,1 9,7 3,13" fill="none" stroke="#fff" stroke-width="1.5"/></svg></div>
</section>

<article class="service abs" style="left:94px">
  <svg width="56" height="58" viewBox="0 0 56 58"><circle cx="24" cy="12" r="10" fill="#555"/><path d="M4 58 C4 36 12 26 24 26 C36 26 44 36 44 58Z" fill="#555"/><circle cx="42" cy="46" r="11" fill="#fff"/><circle cx="42" cy="46" r="9" fill="#6cb52d"/><polyline points="37,46 41,50 47,42" fill="none" stroke="#fff" stroke-width="2.5"/></svg>
  <h3>IT Support &amp; Management</h3>
  <p>At Plumbwick our business is helping organisations to progress team.</p>
</article>
<article class="service abs" style="left:267px">
  <svg width="68" height="58" viewBox="0 0 68 58"><path d="M14 50 C2 50 2 32 14 32 C14 18 30 14 36 22 C44 10 62 16 58 32 C68 34 66 50 56 50Z" fill="#1a9ad6"/><polygon points="34,22 22,36 29,36 29,50 39,50 39,36 46,36" fill="#fff"/></svg>
  <h3>Cloud Computing</h3>
  <p>Plumbwick firmly believe that business requirements IT strategy.</p>
</article>
<article class="service abs" style="left:441px">
  <svg width="58" height="58" viewBox="0 0 58 58"><path d="M29 29 L29 1 A28 28 0 0 0 22 56Z" fill="#a354e0"/><path d="M29 29 L29 1 A28 28 0 0 1 57 29Z" fill="#e98a4f"/><path d="M29 29 L57 29 A28 28 0 0 1 50 47Z" fill="#2ed38a"/><path d="M29 29 L50 47 A28 28 0 0 1 22 56Z" fill="#e8394a"/></svg>
  <h3>Disaster Recovery</h3>
  <p>Plumbwick have expertise in designing the architecture of highly.</p>
</article>
<article class="service abs" style="left:615px">
  <svg width="58" height="58" viewBox="0 0 58 58"><g fill="#9a9a9a"><circle cx="29" cy="29" r="19"/><rect x="25" y="2" width="8" height="54"/><rect x="2" y="25" width="54" height="8"/><rect x="25" y="2" width="8" height="54" transform="rotate(45 29 29)"/><rect x="25" y="2" width="8" height="54" transform="rotate(-45 29 29)"/></g><circle cx="29" cy="29" r="11" fill="#fff"/><circle cx="29" cy="29" r="6" fill="#5c4f6e"/></svg>
  <h3>CAD Services</h3>
  <p>Plumbwick in-house development team build software solutions</p>
</article>

<section class="about abs">
  <h2 class="section-title">About us</h2>
  <p>Plumbwick was established with a specific aim: to consistently deliver an advanced and comprehensive IT service for ambitious growing companies across many industry sectors. We aim to provide the very best in service and support, and to aid business growth through the effective .</p>
  <p>Founded in 2003, we have grown rapidly and have delivered successful business solutions to small and medium sized businesses, working with customers across a wide IT spectrum. The knowledge, experience and expertise which we have gained managing systems and networks for a range of companies over many years enables us to develop with confidence, the best IT solution for our clients.</p>
  <a class="btn">Learn more</a>
</section>

<aside class="news abs">
  <h2>LATEST NEWS</h2>
  <svg class="more" width="7" height="10" viewBox="0 0 7 10"><polyline points="1,1 5,5 1,9" fill="none" stroke="#999" stroke-width="1.6"/></svg>
  <div class="news-item" style="top:48px"><div class="date"><b>02</b><span>Apr</span></div><p>Excepteur sint occaecat cupidatat non proident, sunt in culpa qui officia deserunt mollit anim.</p></div>
  <div class="news-item" style="top:113px"><div class="date"><b>02</b><span>Apr</span></div><p>Excepteur sint occaecat cupidatat non proident, sunt in culpa qui officia deserunt mollit anim.</p></div>
  <div class="news-item" style="top:178px"><div class="date"><b>02</b><span>Apr</span></div><p>Excepteur sint occaecat cupidatat non proident, sunt in culpa qui officia deserunt mollit anim.</p></div>
</aside>

<h2 class="section-title clients-title abs">Our clients</h2>
<div class="client abs" style="left:94px;width:102px">Norland Ashby</div>
<div class="client abs" style="left:212px;width:102px">Veltra</div>
<div class="client abs" style="left:329px;width:146px">Harlow Brandt</div>
<div class="client abs" style="left:491px;width:129px">Oakfield</div>
<div class="client abs" style="left:636px;width:103px">Tarnwell</div>
<svg class="clients-next abs" width="8" height="12" viewBox="0 0 8 12"><polyline points="1,1 6,6 1,11" fill="none" stroke="#aaa" stroke-width="1.8"/></svg>

<footer class="site-footer abs">
  <div class="foot-nav">Home<span>|</span>About us<span>|</span>What we do<span>|</span>News blog<span>|</span>Articles<span>|</span>Clients<span>|</span>Partners<span>|</span>Contact Us</div>
  <div class="copyright">Copyright ©2014 plumbwick. All right reserved.</div>
  <div class="social" aria-label="Social media links"><span></span><span></span><span></span><span></span></div>
</footer>

</body>
</html>
```